Building company buisness cards

We are looking for a sharp modern new look for our business cards.We are a New Zealand based company that specialises in house and land packages.We have attached a photo of the current logo and would like to see if it can be improved somehow if needed.We are open to any colours but we have chosen Black and White at this stage. Feel free to change the font and make the logo smarter looking.Play with the colours and see what looks best.We want a card that looks so good know one will want to throw it away!

Target Market(s)

Building profesonals, home buyers

Industry/Entity Type

Building

Contact Information for Business Card

Garrick Tenwood
0275390628
garrickt@hartvale.co.nz

Font styles to use
Serif
Sans Serif

Colors

Designer to choose colors to be used in the design.

Requirements
Must have
• Just the logo on one side and details on the other
• Clean simple looking card
Nice to have
• Round corners and detail like raised or spot UV
• Something that stands out
Should not have
• To title needed, Director etc

```html
<!DOCTYPE html>
<html lang="en">
<head>
<meta charset="utf-8">
<title>Hartvale Business Card</title>
<link rel="stylesheet" href="https://fonts.googleapis.com/css2?family=Crimson+Pro:wght@400;700&display=swap">
<style>
  :root {
    --page: #dcdcdc;
    --card-light: #ffffff;
    --card-dark: #0b0b0c;
    --card-dark-edge: #1a1a1c;
    --ink: #111111;
    --muted: #4a4a4a;
    --rule: #bdbdbd;
    --mark-light: #ffffff;
  }
  * { box-sizing: border-box; margin: 0; padding: 0; }
  html, body { width: 1125px; height: 1200px; overflow: hidden; background: var(--page); }
  .canvas { position: relative; width: 1125px; height: 1200px; }

  .card {
    position: absolute;
    left: 171px;
    width: 826px;
    height: 470px;
    border-radius: 26px;
    overflow: hidden;
  }
  .card--front { top: 106px; background: var(--card-light); }
  .card--back { top: 639px; background: var(--card-dark); }

  .card__frame {
    position: absolute;
    inset: 18px 22px 16px 22px;
    border: 2.5px solid var(--ink);
    border-radius: 28px;
  }

  .brand {
    position: absolute;
    left: 22px;
    width: 444px;
    top: 198px;
    text-align: center;
    font-family: "Crimson Pro", serif;
    font-weight: 700;
    font-size: 68px;
    line-height: 1;
    color: var(--ink);
  }

  .divider {
    position: absolute;
    left: 466px;
    top: 152px;
    width: 1px;
    height: 168px;
    background: var(--rule);
  }

  .contact {
    position: absolute;
    left: 503px;
    top: 170px;
    font-family: "Crimson Pro", serif;
    color: var(--ink);
  }
  .contact__name {
    font-weight: 700;
    font-size: 29px;
    line-height: 1;
    margin-bottom: 23px;
  }
  .contact__list { list-style: none; }
  .contact__item {
    display: flex;
    align-items: center;
    gap: 10px;
    font-size: 19px;
    line-height: 26px;
    color: var(--muted);
  }
  .contact__icon { width: 17px; height: 17px; fill: var(--ink); flex: none; }

  .back-texture {
    position: absolute;
    inset: 0;
    background: radial-gradient(ellipse at 40% 45%, var(--card-dark-edge), var(--card-dark) 75%);
  }
  .back-name {
    position: absolute;
    right: 56px;
    bottom: 80px;
    font-family: "Crimson Pro", serif;
    font-weight: 700;
    font-size: 28px;
    line-height: 1;
    color: var(--mark-light);
  }
</style>
</head>
<body>
<main class="canvas">
  <section class="card card--front" aria-label="Card front">
    <div class="card__frame"></div>
    <p class="brand">Hartvale</p>
    <div class="divider"></div>
    <div class="contact">
      <p class="contact__name">Garrick Tenwood</p>
      <ul class="contact__list">
        <li class="contact__item">
          <svg class="contact__icon" viewBox="0 0 24 24" aria-hidden="true"><path d="M6.6 10.8a15.1 15.1 0 0 0 6.6 6.6l2.2-2.2c.3-.3.7-.4 1-.2 1.1.4 2.3.6 3.6.6.6 0 1 .4 1 1V20c0 .6-.4 1-1 1A17 17 0 0 1 3 4c0-.6.4-1 1-1h3.5c.6 0 1 .4 1 1 0 1.3.2 2.5.6 3.6.1.3 0 .7-.2 1z"/></svg>
          <span>0275390628</span>
        </li>
        <li class="contact__item">
          <svg class="contact__icon" viewBox="0 0 24 24" aria-hidden="true"><path d="M2 6h20v12H2z M3.5 7.5v.3l8.5 5.7 8.5-5.7v-.3z" fill-rule="evenodd"/></svg>
          <span>garrickt@hartvale.co.nz</span>
        </li>
        <li class="contact__item">
          <svg class="contact__icon" viewBox="0 0 24 24" aria-hidden="true"><path d="M12 2a10 10 0 1 0 0 20 10 10 0 0 0 0-20zm-1 17.9A8 8 0 0 1 4.2 10.8L9 15.6v1c0 1.1.9 2 2 2zm6.9-2.5A2 2 0 0 0 16 16h-1v-3c0-.6-.4-1-1-1H8v-2h2c.6 0 1-.4 1-1V7h2a2 2 0 0 0 2-2v-.4a8 8 0 0 1 2.9 12.8z"/></svg>
          <span>www.hartvale.co.nz</span>
        </li>
      </ul>
    </div>
  </section>

  <section class="card card--back" aria-label="Card back">
    <div class="back-texture" role="img" aria-label="Faint repeating brand pattern across the dark card back"></div>
    <p class="back-name">Hartvale</p>
  </section>
</main>
</body>
</html>
```